LHP Regal Business Card Design 2020

Your Manor Steward is looking for a business card that is clean and straight to the point but still looks high-end and attractive. We are a team comprised of management and field professionals focused on the high-end residential marketplace. We serve homeowners and trade professionals directly based out of the Metrowest/Boston area. We provide client services as well as construction/renovation services.
We are aiming for a black and white feel (white background and black text) and a matte finish with rounded edges.

We want to emphasis our vision of "Properties - Projects - Partners".
Dana Pellham is the president of LHP

Please include the following areas we service: Boston/Cape/Newport
Please make sure to include Dana's mobile (555) 213 4480 & office number (555) 640 1937, email dana@yourmanorsteward.example and website www.yourmanorsteward.example

Colors

Designer to choose only greyscale colors for use in the design.

Requirements
Must have
• Include "Properties - Projects - Partners" in design

Include "After Hours Emergency Support # 1800 555 0142" with icon

```html
<!DOCTYPE html>
<html lang="en">
<head>
<meta charset="utf-8">
<title>LHP Business Card</title>
<link rel="stylesheet" href="https://fonts.googleapis.com/css2?family=Open+Sans:wght@400;600;700&display=swap">
<style>
  :root {
    --page: #e6e6e6;
    --card-dark: #2b2a28;
    --card-light: #f4f4f4;
    --ink: #2a2a2a;
    --ink-soft: #3a3a3a;
    --mark-dark: #1c1c1c;
    --mark-on-dark: #4a4a4a;
    --faint: #dcdcdc;
    --on-dark: #e8e8e8;
  }
  * { margin: 0; padding: 0; box-sizing: border-box; }
  html, body { width: 1200px; height: 960px; overflow: hidden; }
  body {
    background: var(--page);
    font-family: "Open Sans", Arial, sans-serif;
    position: relative;
  }
  .card {
    position: absolute;
    left: 312px;
    width: 580px;
    height: 332px;
    overflow: hidden;
    border-radius: 14px;
  }
  .card-front { top: 128px; background: var(--card-dark); }
  .card-back { top: 511px; background: var(--card-light); }

  .front-name {
    position: absolute;
    left: 0; right: 0; top: 165px;
    text-align: center;
    font-weight: 700;
    font-size: 120px;
    line-height: 1;
    letter-spacing: -2px;
    color: var(--mark-on-dark);
    transform: translateY(-50%);
  }
  .tagline {
    position: absolute;
    left: 0; right: 0; top: 286px;
    text-align: center;
    font-size: 14.5px;
    letter-spacing: 1.6px;
    color: var(--on-dark);
  }

  .brand {
    position: absolute;
    left: 40px; top: 40px;
  }
  .brand-name {
    font-weight: 700;
    font-size: 62px;
    line-height: 1;
    letter-spacing: -1px;
    color: var(--mark-dark);
  }
  .brand-full {
    margin-top: 12px;
    font-weight: 700;
    font-size: 11.5px;
    letter-spacing: 1.2px;
    text-transform: uppercase;
    color: var(--mark-dark);
  }
  .watermark {
    position: absolute;
    right: -6px; bottom: 26px;
    font-weight: 700;
    font-size: 140px;
    line-height: 0.75;
    color: var(--faint);
    letter-spacing: -4px;
  }
  .person {
    position: absolute;
    right: 43px; top: 58px;
    text-align: right;
  }
  .person-name {
    font-weight: 700;
    font-size: 18px;
    color: var(--ink);
    text-transform: uppercase;
  }
  .person-role { font-size: 14.5px; color: var(--ink-soft); margin-top: -1px; }

  .emergency {
    position: absolute;
    right: 43px; top: 118px;
    display: flex;
    align-items: center;
    gap: 7px;
    text-align: right;
    font-size: 12px;
    line-height: 16px;
    color: var(--ink);
  }
  .emergency svg { width: 22px; height: 22px; flex: none; }
  .emergency strong { font-weight: 700; }

  .contacts {
    position: absolute;
    left: 40px; top: 206px;
    list-style: none;
  }
  .contacts li {
    display: flex;
    align-items: center;
    gap: 5px;
    font-size: 14.5px;
    line-height: 19.8px;
    color: var(--ink);
  }
  .contacts svg { width: 13px; height: 13px; flex: none; }

  .areas {
    position: absolute;
    left: 0; right: 0; bottom: 0;
    height: 32px;
    background: var(--card-dark);
    color: var(--on-dark);
    text-align: center;
    font-size: 15px;
    line-height: 29px;
    letter-spacing: 0.4px;
  }
</style>
</head>
<body>
  <section class="card card-front">
    <div class="front-name">LHP</div>
    <p class="tagline">PROPERTIES - PROJECTS - PARTNERS</p>
  </section>

  <section class="card card-back">
    <div class="watermark" aria-hidden="true">LHP</div>
    <div class="brand">
      <div class="brand-name">LHP</div>
      <div class="brand-full">Your Manor Steward</div>
    </div>
    <div class="person">
      <div class="person-name">Dana Pellham</div>
      <div class="person-role">President</div>
    </div>
    <div class="emergency">
      <svg viewBox="0 0 22 22" aria-hidden="true"><path d="M11 2 L21 19.5 H1 Z" fill="none" stroke="#2a2a2a" stroke-width="1.6" stroke-linejoin="round"/><line x1="11" y1="8" x2="11" y2="13.5" stroke="#2a2a2a" stroke-width="1.8" stroke-linecap="round"/><circle cx="11" cy="16.4" r="1.1" fill="#2a2a2a"/></svg>
      <div>After Hours Emergency Support<br><strong># 1800 555 0142</strong></div>
    </div>
    <ul class="contacts">
      <li>
        <svg viewBox="0 0 13 13" aria-hidden="true"><rect x="3" y="0.8" width="7" height="11.4" rx="1.2" fill="none" stroke="#2a2a2a" stroke-width="1.3"/><line x1="5.5" y1="10.3" x2="7.5" y2="10.3" stroke="#2a2a2a" stroke-width="1.1"/></svg>
        (555) 213 4480
      </li>
      <li>
        <svg viewBox="0 0 13 13" aria-hidden="true"><path d="M2.6 0.8 L4.8 0.6 L5.8 3.6 L4.3 4.8 C5 6.5 6.4 7.9 8.1 8.7 L9.3 7.2 L12.3 8.2 L12.1 10.4 C11.9 11.6 10.9 12.3 9.7 12.1 C5.4 11.3 1.6 7.5 0.9 3.2 C0.7 2 1.4 1 2.6 0.8 Z" fill="#2a2a2a"/></svg>
        (555) 640 1937
      </li>
      <li>
        <svg viewBox="0 0 13 13" aria-hidden="true"><rect x="0.7" y="2.3" width="11.6" height="8.4" fill="none" stroke="#2a2a2a" stroke-width="1.2"/><path d="M0.9 2.6 L6.5 7.2 L12.1 2.6" fill="none" stroke="#2a2a2a" stroke-width="1.2"/></svg>
        dana@yourmanorsteward.example
      </li>
      <li>
        <svg viewBox="0 0 13 13" aria-hidden="true"><g fill="none" stroke="#2a2a2a" stroke-width="1"><circle cx="6.5" cy="6.5" r="5.7"/><ellipse cx="6.5" cy="6.5" rx="2.6" ry="5.7"/><line x1="0.8" y1="6.5" x2="12.2" y2="6.5"/><line x1="1.6" y1="3.6" x2="11.4" y2="3.6"/><line x1="1.6" y1="9.4" x2="11.4" y2="9.4"/></g></svg>
        www.yourmanorsteward.example
      </li>
    </ul>
    <div class="areas">Boston | Metrowest | South Shore | Cape | Newport</div>
  </section>
</body>
</html>
```